Tidewell Homecare

I am looking to have a website designed for a housekeeping company that looks similar to this one. https://marloweshomecare.example/

I need 5 websites designed but will start with this one to see how I like it.

Industry/Entity Type

House Cleaning

Coding

Coded - Design and coding required

Number of Pages Required

5+ page

Font styles to use
Serif
Script

Colors
ffffff
fdf9cf
fbf289
fbee3f
d6edf3
86cae7
33a6d7
edf1f8
cedeed

```html
<!DOCTYPE html>
<html lang="en">
<head>
<meta charset="utf-8">
<title>Tidewell Homecare – Services</title>
<link href="https://fonts.googleapis.com/css2?family=Oswald:wght@300;400;500&family=Poppins:wght@300;400;500&display=swap" rel="stylesheet">
<style>
  :root{
    --blue:#0a9be6;
    --blue-dark:#0582d0;
    --ink:#222222;
    --text:#555555;
    --muted:#7a7a7a;
    --card:#f2f2f2;
    --footer:#2b2b2b;
    --footer-text:#a9a9a9;
    --white:#ffffff;
  }
  *{box-sizing:border-box;margin:0;padding:0}
  html,body{width:896px;height:1200px;overflow:hidden;background:var(--white)}
  body{position:relative;font-family:"Poppins",sans-serif;color:var(--text)}

  .site-header{position:absolute;left:0;top:0;width:896px;height:62px;background:var(--white);z-index:3}
  .brand{position:absolute;font-family:"Oswald",sans-serif;font-weight:300;color:var(--ink);line-height:.95;text-transform:uppercase}
  .brand .brand-top{display:block;font-size:24px;letter-spacing:-.5px}
  .brand .brand-bottom{display:block;font-size:13.2px;letter-spacing:.1px}
  .site-header .brand{left:120px;top:7px}
  .main-nav{position:absolute;top:25px;left:0;font-size:8px;letter-spacing:.2px;text-transform:uppercase}
  .main-nav a{position:absolute;white-space:nowrap;color:#444;text-decoration:none}
  .main-nav a.active{color:var(--blue)}
  .call-button{position:absolute;left:652px;top:15px;width:123px;height:31px;border-radius:16px;
    background:linear-gradient(90deg,var(--blue-dark),var(--blue));color:var(--white);
    font-family:"Oswald",sans-serif;font-size:12.5px;display:flex;align-items:center;justify-content:center;gap:5px;letter-spacing:.3px}

  .hero{position:absolute;left:0;top:62px;width:896px;height:330px}
  .hero svg{position:absolute;left:0;top:0}
  .hero-title{position:absolute;left:0;right:0;top:85px;text-align:center;font-family:"Oswald",sans-serif;
    font-weight:400;font-size:46px;color:var(--ink);letter-spacing:-.5px}

  .service-card{position:absolute;width:146px;height:204px;background:var(--card)}
  .service-photo{width:146px;height:98px}
  .service-card h3{position:absolute;left:7px;top:108px;font-weight:400;font-size:9.4px;color:var(--ink);white-space:nowrap;letter-spacing:.1px}
  .service-card ul{position:absolute;left:7px;top:128px;list-style:none;font-size:8px;line-height:14.6px;color:var(--muted);letter-spacing:.2px}
  .service-card li{padding-left:9px;position:relative}
  .service-card li::before{content:"";position:absolute;left:0;top:6px;width:3px;height:3px;border-radius:50%;background:var(--blue)}
  .service-card p{position:absolute;left:9px;top:128px;width:132px;font-size:8px;line-height:14.6px;color:var(--muted);font-weight:300}

  .pricing-button{position:absolute;left:396px;top:898px;width:104px;height:28px;border-radius:14px;
    background:linear-gradient(90deg,var(--blue-dark),var(--blue));color:var(--white);
    font-family:"Oswald",sans-serif;font-size:11px;letter-spacing:.4px;display:flex;align-items:center;justify-content:center}

  .site-footer{position:absolute;left:0;top:963px;width:896px;height:237px}
  .site-footer svg.footer-wave{position:absolute;left:0;top:0}
  .site-footer .brand{left:120px;top:134px;color:var(--white)}
  .copyright{position:absolute;left:121px;top:189px;width:140px;font-size:7.3px;line-height:12.5px;color:var(--footer-text)}
  .copyright strong{font-weight:400;color:#dcdcdc}
  .footer-links{position:absolute;left:292px;top:130px;list-style:none;font-size:7.6px;line-height:19.6px;color:var(--footer-text)}
  .footer-links li:first-child{color:var(--blue)}
  .footer-phone{position:absolute;left:480px;top:124px;font-family:"Oswald",sans-serif;font-size:14.5px;color:var(--white);letter-spacing:.3px}
  .footer-email{position:absolute;left:475px;top:157px;font-size:7.6px;color:var(--footer-text)}
  .footer-icon{position:absolute}
  .social-dot{position:absolute;top:130px;width:25px;height:25px;border-radius:50%;background:var(--white)}
  .social-dot.primary{background:var(--blue)}
</style>
</head>
<body>

<header class="site-header">
  <div class="brand"><span class="brand-top">Tidewell</span><span class="brand-bottom">Homecare</span></div>
  <nav class="main-nav">
    <a style="left:343px">Home</a>
    <a class="active" style="left:393px">Service</a>
    <a style="left:450px">Pricing</a>
    <a style="left:508px">About Us</a>
    <a style="left:573px">Contact Us</a>
  </nav>
  <div class="call-button">
    <svg width="11" height="11" viewBox="0 0 24 24"><path fill="#fff" d="M6.6 10.8a15.1 15.1 0 0 0 6.6 6.6l2.2-2.2a1 1 0 0 1 1-.25 11.4 11.4 0 0 0 3.6.57 1 1 0 0 1 1 1V20a1 1 0 0 1-1 1A17 17 0 0 1 3 4a1 1 0 0 1 1-1h3.5a1 1 0 0 1 1 1c0 1.25.2 2.45.57 3.57a1 1 0 0 1-.25 1z"/></svg>
    123 456 7890
  </div>
</header>

<section class="hero">
  <svg width="896" height="330" viewBox="0 0 1600 590" preserveAspectRatio="none">
    <defs>
      <linearGradient id="heroBg" x1="0" y1="0" x2="1" y2="1">
        <stop offset="0" stop-color="#eef1f1"/>
        <stop offset=".5" stop-color="#f7f6f4"/>
        <stop offset="1" stop-color="#fbfbfb"/>
      </linearGradient>
      <linearGradient id="waveBlue" x1="0" y1="0" x2="1" y2="0">
        <stop offset="0" stop-color="#0582d0"/>
        <stop offset="1" stop-color="#0aa6ee"/>
      </linearGradient>
    </defs>
    <rect width="1600" height="590" fill="url(#heroBg)" role="img" aria-label="Softly faded photo of a set dining table with white bowls and plates"/>
    <path fill="url(#waveBlue)" d="M0,440 C160,540 330,565 480,560 C760,550 950,430 1150,385 C1300,352 1460,360 1600,465 L1600,590 L0,590Z"/>
    <path fill="#ffffff" d="M0,470 C170,560 330,588 480,582 C760,570 960,455 1150,412 C1310,378 1470,395 1600,500 L1600,590 L0,590Z"/>
  </svg>
  <h1 class="hero-title">Services</h1>
</section>

<main>
  <article class="service-card" style="left:120px;top:430px">
    <div class="service-photo" role="img" aria-label="Photo of a bright dining room with a glass table" style="background:linear-gradient(135deg,#d9d2c6,#8a7b6a 60%,#3b4456)"></div>
    <h3>Home Cleaning</h3>
    <ul><li>Weekly</li><li>Bi-Monthly</li><li>Monthly</li><li>As Needed</li></ul>
  </article>
  <article class="service-card" style="left:290px;top:430px">
    <div class="service-photo" role="img" aria-label="Photo of a tidy office desk by a city-view window" style="background:linear-gradient(135deg,#e6e8ea,#c3c7cb 55%,#55595e)"></div>
    <h3>Commercial Cleaning</h3>
    <ul><li>Weekly</li><li>Bi-Monthly</li><li>Monthly</li><li>As Needed</li></ul>
  </article>
  <article class="service-card" style="left:460px;top:430px">
    <div class="service-photo" role="img" aria-label="Photo of a family unpacking moving boxes" style="background:linear-gradient(135deg,#e9e2d8,#c9a683 55%,#6f5a48)"></div>
    <h3>Move-in/Move-out Cleaning</h3>
    <p>Lorem Ipsum is simply dummy text of the printing and typesetting industry.</p>
  </article>
  <article class="service-card" style="left:631px;top:430px">
    <div class="service-photo" role="img" aria-label="Photo of a family walking along the beach" style="background:linear-gradient(180deg,#5cb7c9,#8fd0d8 55%,#d8d4c2)"></div>
    <h3>Vacation Rental Cleaning</h3>
    <ul><li>Weekly</li><li>Departure Cleanings</li><li>Stayover Cleanings</li></ul>
  </article>

  <article class="service-card" style="left:206px;top:660px">
    <div class="service-photo" role="img" aria-label="Photo of a cleaner washing a window" style="background:linear-gradient(135deg,#5d7fa3,#a9c2dc 50%,#2f6fbf)"></div>
    <h3>Window Washing</h3>
    <p>Lorem Ipsum is simply dummy text of the printing and typesetting industry.</p>
  </article>
  <article class="service-card" style="left:375px;top:660px">
    <div class="service-photo" role="img" aria-label="Photo of a worker pressure washing a paved path" style="background:linear-gradient(135deg,#2c4fa0,#5f7c3a 55%,#b9b4ac)"></div>
    <h3>Pressure Washing</h3>
    <p>Lorem Ipsum is simply dummy text of the printing and typesetting industry.</p>
  </article>
  <article class="service-card" style="left:545px;top:660px">
    <div class="service-photo" role="img" aria-label="Photo of a crowd at an evening party" style="background:linear-gradient(135deg,#3a4a86,#1b2145 55%,#6a5c70)"></div>
    <h3>Party/Event Cleanup</h3>
    <p>Lorem Ipsum is simply dummy text of the printing and typesetting industry.</p>
  </article>

  <div class="pricing-button">PRICING</div>
</main>

<footer class="site-footer">
  <svg class="footer-wave" width="896" height="237" viewBox="0 1720 1600 423" preserveAspectRatio="none">
    <path fill="#2b2b2b" d="M0,1780 C150,1868 300,1895 450,1893 C800,1888 1000,1740 1300,1730 C1450,1726 1550,1780 1600,1830 L1600,2143 L0,2143Z"/>
  </svg>
  <div class="brand"><span class="brand-top">Tidewell</span><span class="brand-bottom">Homecare</span></div>
  <p class="copyright">© <strong>Tidewell Homecare</strong> - 2020. All Right Reserved.</p>
  <ul class="footer-links">
    <li>Home</li><li>Service Offered</li><li>About Us</li><li>Contact Us</li>
  </ul>
  <svg class="footer-icon" style="left:460px;top:130px" width="14" height="14" viewBox="0 0 24 24"><path fill="#fff" d="M6.6 10.8a15.1 15.1 0 0 0 6.6 6.6l2.2-2.2a1 1 0 0 1 1-.25 11.4 11.4 0 0 0 3.6.57 1 1 0 0 1 1 1V20a1 1 0 0 1-1 1A17 17 0 0 1 3 4a1 1 0 0 1 1-1h3.5a1 1 0 0 1 1 1c0 1.25.2 2.45.57 3.57a1 1 0 0 1-.25 1z"/></svg>
  <div class="footer-phone">123 456 7890</div>
  <svg class="footer-icon" style="left:460px;top:161px" width="11" height="9" viewBox="0 0 22 18"><rect x="1" y="1" width="20" height="16" rx="2" fill="none" stroke="#a9a9a9" stroke-width="1.6"/><path d="M1.5 2l9.5 8 9.5-8" fill="none" stroke="#a9a9a9" stroke-width="1.6"/></svg>
  <div class="footer-email">info@tidewellhomecare.example</div>
  <span class="social-dot primary" style="left:650px"></span>
  <span class="social-dot" style="left:683px"></span>
  <span class="social-dot" style="left:717px"></span>
  <span class="social-dot" style="left:750px"></span>
</footer>

</body>
</html>
```